Dorla's Cleaners new delivery postcard

We need to advertise for our new pick up and delivery dry cleaning/laundry service.
Mens Business Shirts $2.00
Pants $4.50
Skirts $5.00
Dry Clean Shirt/Blouse $5.00
Dress $9.00
2 Piece Suits $9.00
Updates
We would like to use a 5x7 size postcard, printed on both sides. We would like to add a discount to the card for 25% off of their first order, with the flyer.
We are a famly run dry cleaners. My name is Rosalind Tupper and my cell # is 614-302-7781. We are trying to expand our business to include free pick and delivery.
If possible can you use the logo I sent some where on the postcard? The phone # for the store is 614-295-3064.
Reason: Still need to get partners approval.

```html
<!DOCTYPE html>
<html lang="en">
<head>
<meta charset="utf-8">
<title>Dorla's Cleaners – Delivery Postcard</title>
<link href="https://fonts.googleapis.com/css2?family=Quicksand:wght@500;600;700&display=swap" rel="stylesheet">
<style>
  :root {
    --page-bg: #ebe8e3;
    --card-white: #ffffff;
    --panel-light: #f3f3f3;
    --panel-shade: #e4e4e4;
    --brand-orange: #f37a22;
    --brand-blue: #2a9fd8;
    --brand-green: #6cb33f;
    --ink-navy: #2d5ca8;
    --line-grey: #c9c9c9;
    --stamp-grey: #cfcfcf;
    --placeholder-warm: #e3d6c4;
    --placeholder-cool: #a9c2d6;
    --placeholder-green: #8ab56a;
    --table-glass: rgba(255, 255, 255, 0.84);
  }

  * { box-sizing: border-box; margin: 0; padding: 0; }

  html, body {
    width: 1200px;
    height: 900px;
    overflow: hidden;
  }

  body {
    background: var(--page-bg);
    font-family: "Quicksand", sans-serif;
    position: relative;
  }

  .postcard {
    position: absolute;
    width: 588px;
    height: 420px;
    background: var(--card-white);
    box-shadow: 0 4px 14px rgba(0, 0, 0, 0.18);
    overflow: hidden;
  }

  .postcard--reverse { left: 40px; top: 22px; }
  .postcard--front { left: 572px; top: 452px; }

  .brand {
    position: absolute;
    display: flex;
    align-items: center;
    gap: 8px;
  }
  .brand__dot {
    width: 26px;
    height: 26px;
    border-radius: 50%;
    background: var(--brand-blue);
  }
  .brand__name {
    font-weight: 700;
    font-size: 23px;
    color: var(--brand-orange);
  }

  .phone {
    position: absolute;
    display: flex;
    align-items: center;
    gap: 5px;
    font-weight: 500;
    font-size: 21px;
    color: var(--ink-navy);
  }
  .phone__icon { width: 14px; height: 16px; }

  /* Reverse side */
  .offer-panel {
    position: absolute;
    left: 0;
    top: 0;
    width: 306px;
    height: 372px;
    background: linear-gradient(180deg, var(--panel-light) 0%, var(--panel-shade) 100%);
  }
  .offer-panel .brand { left: 20px; top: 40px; }

  .offer {
    position: absolute;
    left: 40px;
    top: 112px;
    line-height: 1;
  }
  .offer__amount {
    font-weight: 700;
    font-size: 42px;
    color: var(--brand-orange);
  }
  .offer__label {
    font-weight: 700;
    font-size: 24px;
    color: var(--brand-blue);
    margin-top: 2px;
  }
  .offer__terms {
    font-weight: 600;
    font-size: 15px;
    color: var(--brand-green);
    margin-top: 2px;
  }

  .brush-photo {
    position: absolute;
    left: 40px;
    top: 206px;
    width: 232px;
    height: 128px;
    background: var(--placeholder-warm);
  }

  .offer-panel .phone { right: 12px; bottom: 10px; }

  .bottom-strip {
    position: absolute;
    left: 0;
    bottom: 0;
    width: 100%;
    height: 48px;
    background: linear-gradient(180deg, #f7f7f7, #ececec);
  }

  .stamp-box {
    position: absolute;
    right: 24px;
    top: 22px;
    width: 96px;
    height: 112px;
    border: 1px solid var(--stamp-grey);
  }

  .address-lines {
    position: absolute;
    left: 340px;
    top: 226px;
    width: 218px;
    list-style: none;
  }
  .address-lines li {
    height: 32px;
    border-bottom: 1px solid var(--line-grey);
  }

  /* Front side */
  .scene-photo {
    position: absolute;
    left: 0;
    top: 0;
    width: 100%;
    height: 372px;
    background: linear-gradient(180deg, var(--placeholder-cool) 0%, var(--placeholder-green) 100%);
  }

  .postcard--front .brand { left: 18px; top: 28px; }

  .price-table {
    position: absolute;
    left: 20px;
    top: 214px;
    width: 228px;
    padding: 6px 10px 8px 12px;
    background: var(--table-glass);
    color: var(--ink-navy);
    font-weight: 500;
    font-size: 14px;
  }
  .price-table td { padding: 3px 0; }
  .price-table .price { text-align: right; }

  .tagline {
    position: absolute;
    right: 20px;
    top: 258px;
    text-align: right;
    color: #ffffff;
    font-weight: 500;
    font-size: 19px;
    line-height: 1.2;
  }

  .postcard--front .phone { right: 20px; bottom: 12px; }
</style>
</head>
<body>

<section class="postcard postcard--reverse">
  <div class="offer-panel">
    <div class="brand">
      <span class="brand__dot"></span>
      <span class="brand__name">Dorla's Cleaners</span>
    </div>

    <div class="offer">
      <div class="offer__amount">25%</div>
      <div class="offer__label">discount</div>
      <div class="offer__terms">on first order</div>
    </div>

    <div class="brush-photo" role="img" aria-label="Photo of a wooden cleaning brush with natural bristles"></div>

    <div class="phone">
      <svg class="phone__icon" viewBox="0 0 14 16" aria-hidden="true">
        <path d="M3 1 L5.5 1 L6.5 4.5 L4.8 5.8 C5.6 8 6.8 9.6 8.6 10.8 L10 9.2 L13 10.5 L12.6 13.4 C12.4 14.4 11.4 15 10.3 14.8 C5.6 13.6 1.8 9 1 3.6 C0.9 2.2 1.8 1 3 1 Z" fill="var(--brand-green)"/>
      </svg>
      <span>614-302-7781</span>
    </div>
  </div>

  <div class="bottom-strip"></div>
  <div class="stamp-box"></div>
  <ul class="address-lines">
    <li></li><li></li><li></li><li></li>
  </ul>
</section>

<section class="postcard postcard--front">
  <div class="scene-photo" role="img" aria-label="Photo of laundry drying on a clothesline in a sunny green field"></div>

  <div class="bottom-strip"></div>

  <div class="brand">
    <span class="brand__dot"></span>
    <span class="brand__name">Dorla's Cleaners</span>
  </div>

  <table class="price-table">
    <tbody>
      <tr><td>Mens Business Shirts</td><td class="price">$2.00</td></tr>
      <tr><td>Pants</td><td class="price">$4.50</td></tr>
      <tr><td>Skirts</td><td class="price">$5.00</td></tr>
      <tr><td>Dry Clean Shirt/Blouse</td><td class="price">$5.00</td></tr>
      <tr><td>Dress</td><td class="price">$9.00</td></tr>
      <tr><td>2 Piece Suits</td><td class="price">$9.00</td></tr>
    </tbody>
  </table>

  <p class="tagline">free pick up and delivery<br>dry cleaning/laundry</p>

  <div class="phone">
    <svg class="phone__icon" viewBox="0 0 14 16" aria-hidden="true">
      <path d="M3 1 L5.5 1 L6.5 4.5 L4.8 5.8 C5.6 8 6.8 9.6 8.6 10.8 L10 9.2 L13 10.5 L12.6 13.4 C12.4 14.4 11.4 15 10.3 14.8 C5.6 13.6 1.8 9 1 3.6 C0.9 2.2 1.8 1 3 1 Z" fill="var(--brand-green)"/>
    </svg>
    <span>614-302-7781</span>
  </div>
</section>

</body>
</html>
```